Biz Card Design TVCP

New business card for a new company.
Logo was completed by a designer on ArtHarbor and looking to continue requesting additional services.
Company Name: Tidal Vector Power Consulting
Although this company is starting in Canada, we will be moving towards a global presence within the next 6 months.
Key elements to this business are as follows.
Energy Procurement
Energy Reduction Services
Demand Side Consulting
Energy Efficiency Consulting
Saving Clients Money
Helping Them Go "Green"
Managing Their Energy Requirements
Basically the goal for our company is to find the best procurement solution for our clients and reduce their energy consumption. This reduces their expenses and the amount of greenhouse gas they produce on a daily basis.
I have been in the energy footprint for the last 20 years and know that most companies are looking to "do whatever is necessary to get them to sign on the dotted line". I would prefer to walk away from a client that I can't help than to put them into a situation that they will regret for years to come. This is where the "TIDAL" part of the company name comes from.
The following is a catch phrase that encompasses what we do.
"Reducing your carbon footprint & energy bill at the same time!"
The back of the card needs to have this statement along with some sort of illustration. The back is a playground for creative ideas.
The front of the card needs the following.
Logo.
First & Last Name (Gus Marwick)
Title (Energy Warrior)
Phone Number (555) 314-2718
Fax Number (555) 271-8314
Email Address gus@tidalvectorpowerconsulting.example
Address 47 fenwick rd Toronto Ontario K4T 2P9
I want it to be a card that is remembered when any of my staff give it to a customer. It HAS to stand out.
Target Market(s)
Business Owners, Decision Makers, 30 to 65+
Industry/Entity Type
Business
Look and feel

```html
<!DOCTYPE html>
<html lang="en">
<head>
<meta charset="utf-8">
<title>Tidal Vector Power Consulting – Business Card</title>
<link href="https://fonts.googleapis.com/css2?family=Open+Sans:wght@400;600;700&display=swap" rel="stylesheet">
<style>
  :root {
    --stage: #e9e6e1;
    --ink-black: #0b0b0b;
    --black-glow: #2e2e2e;
    --leaf-green: #22b04b;
    --soft-green: #7fcf6a;
    --brand-blue: #3d6cc0;
    --tag-yellow: #e6dc5a;
    --paper: #ffffff;
    --text-dark: #222222;
  }
  * { box-sizing: border-box; margin: 0; padding: 0; }
  html, body { width: 1200px; height: 900px; overflow: hidden; }
  body {
    background: var(--stage);
    font-family: "Open Sans", Arial, sans-serif;
    position: relative;
  }
  .card {
    position: absolute;
    top: 296px;
    width: 540px;
    height: 309px;
    overflow: hidden;
    box-shadow: 0 6px 18px rgba(0,0,0,.25);
  }
  /* ---------- back ---------- */
  .card-back {
    left: 40px;
    background: radial-gradient(ellipse at 55% 35%, var(--black-glow) 0%, var(--ink-black) 70%);
  }
  .back-wordmark {
    position: absolute; left: 28px; top: 34px;
    font-weight: 700; font-size: 23px; letter-spacing: -.5px;
    color: var(--brand-blue);
  }
  .service-list {
    position: absolute; left: 32px; top: 92px;
    list-style: none;
  }
  .service-list li {
    display: flex; align-items: center; gap: 10px;
    font-size: 13px; color: var(--leaf-green);
    line-height: 22px;
  }
  .service-list li::before {
    content: ""; width: 9px; height: 9px; border-radius: 50%;
    background: var(--soft-green);
  }
  .back-tagline {
    position: absolute; right: 24px; bottom: 22px;
    font-size: 12px; color: var(--tag-yellow);
  }
  /* ---------- front ---------- */
  .card-front { left: 620px; background: var(--paper); }
  .front-swoosh { position: absolute; inset: 0; }
  .front-wordmark {
    position: absolute; left: 34px; top: 128px;
    font-weight: 700; font-size: 21px; letter-spacing: -.5px;
    color: var(--brand-blue);
    display: flex; align-items: center; gap: 8px;
  }
  .front-wordmark .mark-dot {
    width: 14px; height: 14px; border-radius: 50%; background: var(--leaf-green);
  }
  .person { position: absolute; left: 34px; top: 196px; }
  .person-name { font-weight: 700; font-size: 21px; color: var(--leaf-green); line-height: 1.1; }
  .person-title { font-weight: 600; font-size: 14px; color: var(--brand-blue); }
  .contact {
    position: absolute; right: 22px; top: 22px;
    list-style: none; text-align: right;
  }
  .contact li {
    display: flex; justify-content: flex-end; align-items: center; gap: 7px;
    font-size: 11px; color: var(--text-dark); line-height: 19px;
  }
  .contact svg { width: 12px; height: 12px; flex: none; }
</style>
</head>
<body>

<section class="card card-back" aria-label="Card back">
  <div class="back-wordmark">TidalVectorPowerConsulting</div>
  <ul class="service-list">
    <li>Energy Procurement</li>
    <li>Energy Reduction Services</li>
    <li>Demand Side Consulting</li>
    <li>Energy Efficiency Consulting</li>
    <li>Saving Clients Money</li>
    <li>Helping Them Go "Green"</li>
    <li>Managing Their Energy Requirements</li>
  </ul>
  <p class="back-tagline">"Reducing your carbon footprint &amp; energy bill at the same time!"</p>
</section>

<section class="card card-front" aria-label="Card front">
  <svg class="front-swoosh" viewBox="0 0 540 309" aria-hidden="true">
    <path d="M110,309 C300,292 470,215 540,80 L540,309 Z" fill="var(--brand-blue)"/>
    <path d="M125,309 C310,296 475,225 540,96 L540,309 Z" fill="var(--paper)"/>
    <path d="M138,309 C318,300 480,235 540,108 L540,309 Z" fill="var(--leaf-green)"/>
    <path id="tagline-curve" d="M215,304 C360,292 470,240 532,150" fill="none"/>
    <text font-family="Open Sans, Arial, sans-serif" font-size="10.5" fill="#ffffff">
      <textPath href="#tagline-curve">"Reducing your carbon footprint &amp; energy bill at the same time!"</textPath>
    </text>
  </svg>

  <div class="front-wordmark"><span class="mark-dot"></span>TidalVectorPowerConsulting</div>

  <div class="person">
    <div class="person-name">Gus Marwick</div>
    <div class="person-title">Energy Warrior</div>
  </div>

  <ul class="contact">
    <li>(555) 314-2718
      <svg viewBox="0 0 12 12"><rect x=".5" y=".5" width="11" height="11" rx="2" fill="none" stroke="var(--leaf-green)"/><path d="M3.5 3 L5 3 L5.5 4.5 L4.7 5.2 Q5.6 6.6 6.8 7.3 L7.5 6.5 L9 7 L9 8.5 Q5 8.8 3.5 3 Z" fill="var(--brand-blue)"/></svg></li>
    <li>(555) 271-8314
      <svg viewBox="0 0 12 12"><rect x=".5" y=".5" width="11" height="11" rx="2" fill="none" stroke="var(--leaf-green)"/><rect x="3" y="4.5" width="6" height="4" fill="var(--brand-blue)"/><rect x="4" y="2.5" width="4" height="2" fill="var(--brand-blue)"/></svg></li>
    <li>gus@tidalvectorpowerconsulting.example
      <svg viewBox="0 0 12 12"><rect x=".5" y=".5" width="11" height="11" rx="2" fill="none" stroke="var(--leaf-green)"/><rect x="2.5" y="3.5" width="7" height="5" fill="var(--brand-blue)"/><path d="M2.5 3.5 L6 6.3 L9.5 3.5" fill="none" stroke="#fff" stroke-width=".8"/></svg></li>
    <li>47 fenwick rd Toronto Ontario K4T 2P9
      <svg viewBox="0 0 12 12"><rect x=".5" y=".5" width="11" height="11" rx="2" fill="none" stroke="var(--leaf-green)"/><path d="M6 10 C4 7.5 3.3 6.3 3.3 5 A2.7 2.7 0 0 1 8.7 5 C8.7 6.3 8 7.5 6 10 Z" fill="var(--brand-blue)"/><circle cx="6" cy="5" r="1" fill="#fff"/></svg></li>
  </ul>
</section>

</body>
</html>
```